New Business Card Design Project

Use the flyer uploaded and website www.brightoakbuilders.com for inspiration.
List Our Services on Backside of business cards
Marcus Delling
Harborline Builders Inc.
Licensed General Contractors
858-471-6093

Contact Information for Business Card

Use the flyer uploaded and website www.brightoakbuilders.com for inspiration. List Our Services on Backside of business cards Marcus Delling Harborline Builders Inc. Licensed General Contractors 858-471-6093

```html
<!DOCTYPE html>
<html lang="en">
<head>
<meta charset="utf-8">
<title>Harborline Builders – Business Card</title>
<link href="https://fonts.googleapis.com/css2?family=Montserrat:wght@400;500;600;700&display=swap" rel="stylesheet">
<style>
  :root {
    --page-bg: #e9e6e1;
    --card-front: #ffffff;
    --card-back: #252525;
    --ink: #111111;
    --ink-soft: #1c1c1c;
    --light: #ffffff;
    --light-soft: #e6e6e6;
    --rule: #bdbdbd;
  }
  * { margin: 0; padding: 0; box-sizing: border-box; }
  html, body {
    width: 900px; height: 1200px; overflow: hidden;
    background: var(--page-bg);
    font-family: "Montserrat", Arial, sans-serif;
  }
  .canvas { position: relative; width: 900px; height: 1200px; }
  .card {
    position: absolute; border-radius: 22px;
    box-shadow: 0 8px 18px rgba(0,0,0,0.25);
  }
  .card--front { left: 80px; top: 131px; width: 742px; height: 440px; background: var(--card-front); color: var(--ink); }
  .card--back { left: 78px; top: 638px; width: 744px; height: 440px; background: var(--card-back); color: var(--light); }

  .person { position: absolute; left: 38px; top: 40px; }
  .person__name { font-size: 26px; font-weight: 700; line-height: 1.1; }
  .person__title { font-size: 15.5px; font-weight: 400; margin-top: 2px; }

  .brand-name {
    position: absolute; text-align: center; text-transform: uppercase;
    font-weight: 600; letter-spacing: 1px; white-space: nowrap;
  }
  .card--front .brand-name { left: 355px; width: 325px; top: 205px; font-size: 25px; color: var(--ink); }
  .card--back .brand-name { left: 20px; width: 350px; top: 270px; font-size: 25px; color: var(--light); }

  .contact { position: absolute; left: 42px; top: 280px; list-style: none; }
  .contact__item { display: flex; align-items: center; height: 28.5px; font-size: 15.5px; color: var(--ink-soft); }
  .contact__icon { width: 16px; height: 16px; margin-right: 16px; fill: var(--ink); }
  .license { position: absolute; left: 43px; top: 383px; font-size: 15.5px; color: var(--ink-soft); }

  .services { position: absolute; left: 396px; top: 113px; }
  .services__heading {
    font-size: 20px; font-weight: 700; padding-bottom: 6px;
    border-bottom: 1px solid var(--rule); display: inline-block; width: 139px;
  }
  .services__list { list-style: none; margin-top: 10px; }
  .services__item {
    position: relative; padding-left: 20px; font-size: 15.5px;
    line-height: 24.3px; color: var(--light-soft);
  }
  .services__item::before {
    content: ""; position: absolute; left: 3px; top: 10px;
    width: 5px; height: 5px; border-radius: 50%; background: var(--light-soft);
  }
</style>
</head>
<body>
<main class="canvas">
  <section class="card card--front" aria-label="Business card front">
    <div class="person">
      <h1 class="person__name">Marcus Delling</h1>
      <p class="person__title">Managing Director</p>
    </div>
    <div class="brand-name">Harborline Builders</div>
    <ul class="contact">
      <li class="contact__item">
        <svg class="contact__icon" viewBox="0 0 16 16" aria-hidden="true"><path d="M2 5c0-2 2-3 6-3s6 1 6 3v1h-3V5H5v1H2z"/><path d="M4 7h8l2 7H2z"/><circle cx="8" cy="10.5" r="1.6" fill="#fff"/></svg>
        858-471-6093
      </li>
      <li class="contact__item">
        <svg class="contact__icon" viewBox="0 0 16 16" aria-hidden="true"><path d="M1 3h14v1.5L8 9 1 4.5z"/><path d="M1 6l7 4.5L15 6v7H1z"/></svg>
        info@brightoakbuilders.com
      </li>
      <li class="contact__item">
        <svg class="contact__icon" viewBox="0 0 16 16" aria-hidden="true"><circle cx="8" cy="8" r="7"/><path d="M5 4c1 0 2 1 1.5 2S4 7 4.5 8.5 6 10 5.5 12" stroke="#fff" stroke-width="1.2" fill="none"/><path d="M11 3.5c-1 1 0 2 1 2.5M12.5 10c-1 0-2 1-1.5 2.5" stroke="#fff" stroke-width="1.2" fill="none"/></svg>
        www.brightoakbuilders.com
      </li>
    </ul>
    <p class="license">CSLB Licensed No. #1048265</p>
  </section>

  <section class="card card--back" aria-label="Business card back">
    <div class="brand-name">Harborline Builders</div>
    <div class="services">
      <h2 class="services__heading">Our Services</h2>
      <ul class="services__list">
        <li class="services__item">Remodel: Kitchen &amp; Bath</li>
        <li class="services__item">Painting: Interior &amp; Exterior</li>
        <li class="services__item">Flooring: Carpet, Vinyl, Wood</li>
        <li class="services__item">Window: Door Replacement</li>
        <li class="services__item">Plumbing: Repair &amp; Upgrades</li>
        <li class="services__item">Energy Efficienct Upgrades</li>
        <li class="services__item">Deck &amp; Patio consturction</li>
        <li class="services__item">Water &amp; Mold Damage</li>
        <li class="services__item">Garage Renovation</li>
      </ul>
    </div>
  </section>
</main>
</body>
</html>
```